Building company buisness cards

We are looking for a sharp modern new look for our business cards.We are a New Zealand based company that specialises in house and land packages.We have attached a photo of the current logo and would like to see if it can be improved somehow if needed.We are open to any colours but we have chosen Black and White at this stage. Feel free to change the font and make the logo smarter looking.Play with the colours and see what looks best.We want a card that looks so good know one will want to throw it away!

Target Market(s)

Building profesonals, home buyers

Industry/Entity Type

Building

Contact Information for Business Card

Garrick Tenwood
0275390628
garrickt@hartvale.co.nz

Font styles to use
Serif
Sans Serif

Colors

Designer to choose colors to be used in the design.

Requirements
Must have
• Just the logo on one side and details on the other
• Clean simple looking card
Nice to have
• Round corners and detail like raised or spot UV
• Something that stands out
Should not have
• To title needed, Director etc

```html
<!DOCTYPE html>
<html lang="en">
<head>
<meta charset="utf-8">
<title>Hartvale business cards</title>
<link rel="stylesheet" href="https://fonts.googleapis.com/css2?family=Playfair+Display:wght@700;900&family=Lato:wght@400&display=swap">
<style>
  :root {
    --backdrop: #666666;
    --card: #0b0c11;
    --ink: #ffffff;
    --ink-soft: #e4e4e6;
    --rule: #6c6d72;
  }
  html, body {
    margin: 0;
    padding: 0;
    width: 1200px;
    height: 900px;
    overflow: hidden;
    background: var(--backdrop);
  }
  .stage {
    position: relative;
    width: 1200px;
    height: 900px;
  }
  .card {
    position: absolute;
    top: 275px;
    width: 478px;
    height: 295px;
    background: var(--card);
    border-radius: 0 52px 0 52px;
    color: var(--ink);
  }
  .card--details { left: 120px; }
  .card--brand { left: 619px; }

  .wordmark {
    font-family: "Playfair Display", Georgia, serif;
    font-weight: 900;
    letter-spacing: -0.5px;
    line-height: 1;
    color: var(--ink);
    margin: 0;
  }
  .card--details .wordmark {
    position: absolute;
    left: 0;
    right: 0;
    top: 76px;
    text-align: center;
    font-size: 52px;
  }
  .brand-lockup {
    position: absolute;
    left: 102px;
    top: 100px;
  }
  .card--brand .wordmark {
    font-size: 68px;
  }
  .tagline {
    margin: 4px 0 0 3px;
    font-family: "Lato", Arial, sans-serif;
    font-size: 14.5px;
    letter-spacing: 0.4px;
    color: var(--ink-soft);
  }

  .holder {
    position: absolute;
    left: 0;
    right: 0;
    top: 183px;
    text-align: center;
  }
  .holder__name {
    margin: 0;
    font-family: "Playfair Display", Georgia, serif;
    font-weight: 700;
    font-size: 21px;
    letter-spacing: 0.3px;
  }
  .holder__rule {
    width: 125px;
    height: 1px;
    margin: 11px auto 10px;
    background: var(--rule);
    border: 0;
  }
  .holder__contact {
    margin: 0;
    font-family: "Lato", Arial, sans-serif;
    font-size: 13.5px;
    line-height: 18px;
    color: var(--ink-soft);
  }
</style>
</head>
<body>
  <main class="stage">
    <section class="card card--details" aria-label="Card back with contact details">
      <p class="wordmark">Hartvale</p>
      <div class="holder">
        <p class="holder__name">Garrick Tenwood</p>
        <hr class="holder__rule">
        <p class="holder__contact">P: 0275390628<br>E: garrickt@hartvale.co.nz</p>
      </div>
    </section>

    <section class="card card--brand" aria-label="Card front with name and tagline">
      <div class="brand-lockup">
        <p class="wordmark">Hartvale</p>
        <p class="tagline">Houses shaped for you.</p>
      </div>
    </section>
  </main>
</body>
</html>
```